Letterhead, stationery and email signature for construction business

I need the letterhead, stationery and email signature designs for a construction business. I want them to have a corporate feel to them.

I've attached the logo for reference.

```html
<!DOCTYPE html>
<html lang="en">
<head>
<meta charset="utf-8">
<title>Halden Build — Business Card</title>
<link href="https://fonts.googleapis.com/css2?family=Montserrat:wght@600;700&family=Roboto:wght@400&display=swap" rel="stylesheet">
<style>
  :root {
    --bg: #4a4b4e;
    --brand-blue: #2d4fa3;
    --brand-blue-deep: #233f94;
    --brand-blue-light: #3a66b8;
    --ink-grey: #55565c;
    --text-grey: #6b6c70;
    --rule: #8a8b8f;
    --paper: #ffffff;
  }
  * { box-sizing: border-box; margin: 0; padding: 0; }
  html, body { width: 1200px; height: 780px; overflow: hidden; }
  body {
    background: var(--bg);
    display: flex;
    align-items: center;
    justify-content: center;
    gap: 40px;
  }
  .card {
    width: 540px;
    height: 309px;
    position: relative;
    box-shadow: 0 10px 28px rgba(0,0,0,0.45);
  }
  .card-back {
    background: linear-gradient(160deg, var(--brand-blue-deep) 0%, var(--brand-blue) 55%, var(--brand-blue-light) 100%);
  }
  .card-front {
    background: var(--paper);
    font-family: "Roboto", Arial, sans-serif;
  }
  .wordmark {
    position: absolute;
    top: 58px;
    left: 0;
    right: 0;
    display: flex;
    align-items: center;
    justify-content: center;
    gap: 14px;
  }
  .wordmark-square {
    width: 46px;
    height: 46px;
    background: var(--brand-blue);
  }
  .wordmark-name {
    font-family: "Montserrat", Arial, sans-serif;
    font-weight: 700;
    font-size: 38px;
    letter-spacing: 1px;
    color: var(--brand-blue);
  }
  .details {
    position: absolute;
    top: 150px;
    left: 0;
    right: 0;
    display: flex;
    justify-content: center;
    align-items: stretch;
    gap: 22px;
  }
  .person { text-align: right; align-self: flex-end; padding-bottom: 2px; }
  .person-name {
    font-family: "Montserrat", Arial, sans-serif;
    font-weight: 700;
    font-size: 17px;
    color: var(--brand-blue);
    letter-spacing: 0.3px;
  }
  .person-title {
    font-family: "Montserrat", Arial, sans-serif;
    font-weight: 600;
    font-size: 13px;
    color: var(--text-grey);
    margin-top: 2px;
  }
  .divider { width: 1px; background: var(--rule); }
  .contacts { list-style: none; font-size: 13.5px; color: var(--ink-grey); }
  .contacts li { display: flex; align-items: center; gap: 7px; line-height: 22px; }
  .contacts svg { width: 13px; height: 13px; flex: none; }
  .address {
    position: absolute;
    bottom: 44px;
    left: 0;
    right: 0;
    display: flex;
    justify-content: center;
    align-items: center;
    gap: 8px;
    font-size: 15px;
    color: var(--text-grey);
  }
  .address svg { width: 14px; height: 19px; }
</style>
</head>
<body>
  <div class="card card-back" role="img" aria-label="Repeating tiled brand-mark pattern in shades of blue"></div>

  <div class="card card-front">
    <div class="wordmark">
      <span class="wordmark-square"></span>
      <span class="wordmark-name">HALDEN BUILD</span>
    </div>

    <div class="details">
      <div class="person">
        <div class="person-name">MARCUS T. ELLING</div>
        <div class="person-title">Founder &amp; CEO</div>
      </div>
      <div class="divider"></div>
      <ul class="contacts">
        <li>
          <svg viewBox="0 0 24 24" fill="var(--brand-blue)"><path d="M6.6 10.8a15 15 0 0 0 6.6 6.6l2.2-2.2a1 1 0 0 1 1-.25 11.4 11.4 0 0 0 3.6.57 1 1 0 0 1 1 1V20a1 1 0 0 1-1 1A17 17 0 0 1 3 4a1 1 0 0 1 1-1h3.5a1 1 0 0 1 1 1c0 1.25.2 2.45.57 3.57a1 1 0 0 1-.25 1z"/></svg>
          (555)310-0182
        </li>
        <li>
          <svg viewBox="0 0 24 24" fill="none" stroke="var(--brand-blue)" stroke-width="2"><rect x="2" y="5" width="20" height="14"/><path d="M2 5l10 8 10-8"/></svg>
          info@haldenbuild.com
        </li>
        <li>
          <svg viewBox="0 0 24 24" fill="none" stroke="var(--brand-blue)" stroke-width="1.8"><circle cx="12" cy="12" r="10"/><ellipse cx="12" cy="12" rx="4.5" ry="10"/><path d="M2 12h20M4 7h16M4 17h16"/></svg>
          www.haldenbuild.com
        </li>
      </ul>
    </div>

    <div class="address">
      <svg viewBox="0 0 14 19" fill="var(--brand-blue)"><path d="M7 0a7 7 0 0 0-7 7c0 5 7 12 7 12s7-7 7-12a7 7 0 0 0-7-7zm0 9.5A2.5 2.5 0 1 1 7 4.5a2.5 2.5 0 0 1 0 5z"/></svg>
      2470 Fairmont Park Road, Lakeview, CA 90412
    </div>
  </div>
</body>
</html>
```